Fern Gate book design

I would like a new cover design to my book Fern Gate. It is a self help book for teenagers that I give away in public schools while I speak on suicide prevention type topics. I will send you the current cover that has the Fern Gate logo on it. The tag line now says, "raising the value of human life" I want to change that to, "Understanding your true value."

```html
<!DOCTYPE html>
<html lang="en">
<head>
<meta charset="utf-8">
<title>Fern Gate – Book Cover</title>
<link href="https://fonts.googleapis.com/css2?family=Source+Sans+3:wght@400;600;700&display=swap" rel="stylesheet">
<style>
  :root {
    --backdrop: #262626;
    --cover-top: #efefee;
    --cover-mid: #e2dfdf;
    --cover-rose: #cfb0b1;
    --cover-bottom: #9a3b3f;
    --crowd-light: #d9aaa5;
    --crowd-mid: #c48580;
    --crowd-deep: #a8504f;
    --crowd-dark: #8f3a3c;
    --wordmark: #474747;
    --accent-red: #9b0d12;
    --tagline: #1e1e1e;
    --author: #ffffff;
  }
  html, body {
    margin: 0;
    padding: 0;
    width: 1200px;
    height: 1200px;
    overflow: hidden;
    background: var(--backdrop);
  }
  .canvas {
    position: relative;
    width: 1200px;
    height: 1200px;
  }
  .cover {
    position: absolute;
    left: 248px;
    top: 55px;
    width: 704px;
    height: 1090px;
    overflow: hidden;
    background: linear-gradient(180deg,
      var(--cover-top) 0%,
      var(--cover-top) 35%,
      var(--cover-mid) 52%,
      var(--cover-rose) 62%,
      var(--cover-bottom) 100%);
    font-family: "Source Sans 3", "Myriad Pro", sans-serif;
  }
  .crowd-photo {
    position: absolute;
    left: 0;
    bottom: 0;
    width: 100%;
    height: 470px;
    background:
      radial-gradient(ellipse 45% 30% at 92% 8%, rgba(240,220,218,0.55) 0%, rgba(240,220,218,0) 100%),
      radial-gradient(ellipse 60% 40% at 25% 55%, rgba(222,160,150,0.7) 0%, rgba(222,160,150,0) 100%),
      radial-gradient(ellipse 55% 40% at 75% 60%, rgba(150,70,72,0.55) 0%, rgba(150,70,72,0) 100%),
      linear-gradient(180deg,
        rgba(201,150,150,0) 0%,
        var(--crowd-light) 22%,
        var(--crowd-mid) 48%,
        var(--crowd-deep) 78%,
        var(--crowd-dark) 100%);
  }
  .brand {
    position: absolute;
    left: 118px;
    top: 212px;
    display: inline-flex;
    flex-direction: column;
    align-items: flex-end;
  }
  .brand-title {
    display: flex;
    align-items: center;
    gap: 16px;
  }
  .brand-dot {
    width: 34px;
    height: 34px;
    border-radius: 50%;
    background: var(--accent-red);
    flex: none;
  }
  .brand-name {
    font-size: 92px;
    font-weight: 600;
    line-height: 1;
    letter-spacing: 1px;
    color: var(--wordmark);
    white-space: nowrap;
  }
  .tagline {
    margin: 10px 0 0;
    font-size: 18px;
    font-weight: 400;
    color: var(--tagline);
    white-space: nowrap;
  }
  .credits {
    position: absolute;
    left: 0;
    width: 100%;
    top: 968px;
    text-align: center;
    color: var(--author);
  }
  .authors {
    margin: 0;
    font-size: 26px;
    font-weight: 700;
    line-height: 1.2;
  }
  .foreword {
    margin: 6px 0 0;
    font-size: 17px;
    font-weight: 400;
  }
</style>
</head>
<body>
  <div class="canvas">
    <section class="cover">
      <div class="crowd-photo" role="img" aria-label="Photo of a large audience at a youth event with hands raised, tinted red"></div>

      <div class="brand">
        <div class="brand-title">
          <span class="brand-dot"></span>
          <span class="brand-name">Fern Gate</span>
        </div>
        <p class="tagline">Understanding your True Value</p>
      </div>

      <div class="credits">
        <p class="authors">Glen Archer with Reid Calloway</p>
        <p class="foreword">Forward by Westbrook survivor, Owen Pryce</p>
      </div>
    </section>
  </div>
</body>
</html>
```